Website mockup using figma or other design software for Plumbing Company

We are looking for a talented UI/UX designer to create a high-converting, modern, and professional website design for a local plumbing company. The goal is to move away from the "dated" look of traditional trades and provide a seamless, trustworthy experience for homeowners and commercial clients.
The Challenge
Create a Homepage and a Service Page design that balances professional expertise with an urgent "call-to-action" (CTA) focus. We need a design that looks great on desktop but is built with a mobile-first mindset, as most customers find plumbers via their phones during emergencies.
This company will focus more on B2B, and corporate contracts, but should still be friendly to the public.
Here are some examples of what we are looking for
https://velotrin-works.com/construction/plumbing-construction/
https://velotrin-works.com/
The company is called "KT Plumbing."
Please see the logo below.

```html
<!DOCTYPE html>
<html lang="en">
<head>
<meta charset="utf-8">
<title>Velotrin — MEP Expertise</title>
<link href="https://fonts.googleapis.com/css2?family=Figtree:wght@400;500;600;700;800&display=swap" rel="stylesheet">
<style>
:root{
  --navy:#071826;
  --blue:#2a6cb0;
  --blue-soft:#dce9f5;
  --ink:#1b1f24;
  --muted:#3b4350;
  --white:#ffffff;
  --line:#d5dbe2;
  --dot-light:#8fa0b3;
}
*{box-sizing:border-box;margin:0;padding:0}
html,body{width:1200px;height:3610px;overflow:hidden}
body{position:relative;background:var(--white);font-family:"Figtree",sans-serif;color:var(--ink)}
.abs{position:absolute}
.brand{display:flex;align-items:center;gap:9px;font-weight:800;font-size:25px;letter-spacing:.5px}
.brand-mark{width:22px;height:22px;background:currentColor}
.btn{position:absolute;display:flex;align-items:center;justify-content:center;font-size:13px;font-weight:500;letter-spacing:.3px;clip-path:polygon(6% 0,100% 0,94% 50%,100% 100%,6% 100%,0 50%)}
.btn-light{background:var(--white);color:var(--navy)}
.btn-dark{background:var(--navy);color:var(--white);clip-path:polygon(0 0,94% 0,100% 50%,94% 100%,0 100%,6% 50%)}
.ph{position:absolute}
.underline{position:absolute;height:3px;background:var(--blue);width:56px}

/* hero */
.hero{position:absolute;left:0;top:0;width:1200px;height:600px;background:linear-gradient(160deg,#0f2a40,#061624 70%)}
.nav{position:absolute;top:48px;left:493px;display:flex;gap:27px;color:var(--white);font-size:14px;font-weight:500}
.hero-title{left:578px;top:140px;color:var(--white);font-size:35px;font-weight:700;line-height:54px;letter-spacing:-.5px}
.hero-title span{color:#3a84cf}
.hero-text{left:579px;top:292px;width:520px;color:var(--white);font-size:15px;line-height:35px}

/* about */
.h2{font-size:31px;font-weight:700;letter-spacing:-.5px}
.about-head{display:flex;align-items:center;gap:22px}
.about-head .rule{width:56px;height:3px;background:var(--blue)}
.about-text{left:112px;top:672px;width:432px;font-size:15px;line-height:34.5px;text-align:justify;color:var(--muted)}
.about-text p+p{margin-top:8px}

/* services */
.card{position:absolute;top:1328px;width:303px;height:354px;border:1.5px dashed var(--dot-light);border-radius:6px 6px 6px 60px;color:var(--white);text-align:center}
.card .ph{left:5px;top:5px;width:290px;height:190px;border-radius:4px}
.card h3{position:absolute;top:221px;width:100%;font-size:16px;font-weight:600}
.card p{position:absolute;top:255px;left:30px;right:30px;font-size:14px;line-height:33px}
.circle-btn{position:absolute;left:137px;bottom:-14px;width:29px;height:29px;border-radius:50%;background:var(--white)}

/* why */
.why-item{position:absolute;width:310px}
.why-item h4{color:var(--blue);font-size:15px;font-weight:500;letter-spacing:.3px;margin-bottom:14px}
.why-item p{font-size:15px;line-height:34px;color:var(--muted)}

/* blog */
.post{position:absolute;top:2733px;width:304px;color:var(--white)}
.post .ph{left:0;top:0;width:304px;height:235px;border-radius:4px 4px 40px 4px}
.post .date{position:absolute;left:-6px;top:223px;background:var(--white);color:var(--navy);font-size:13px;padding:5px 18px;clip-path:polygon(6% 0,100% 0,94% 100%,0 100%)}
.post p{position:absolute;top:262px;font-size:14.5px;line-height:34.5px;width:304px}

/* footer */
.foot-links{left:0;width:1200px;top:3403px;text-align:center;font-size:13.5px;color:var(--navy)}
.social{position:absolute;top:3512px;width:33px;height:33px;border:1.5px solid var(--navy);border-radius:50%}
</style>
</head>
<body>

<!-- HERO -->
<section class="hero">
  <div class="ph" role="img" aria-label="Industrial pipework backdrop" style="inset:0;background:linear-gradient(120deg,rgba(30,60,90,.5),rgba(5,20,35,.2))"></div>
  <div class="abs brand" style="left:112px;top:40px;color:var(--white)"><span class="brand-mark"></span>VELOTRIN</div>
  <nav class="nav"><span>VT SERVICE</span><span>VT MEP</span><span>PROJECTS</span><span>CAREERS</span><span>ABOUT</span><span>BLOG</span><span>CONTACT</span></nav>
  <div class="ph" role="img" aria-label="Smiling plumber in hard hat with arms crossed" style="left:105px;top:105px;width:273px;height:400px;border-radius:120px 120px 0 0;background:linear-gradient(180deg,#c9a24a 0%,#8a6a52 30%,#5a5048 70%,#3a3630)"></div>
  <h1 class="abs hero-title">PROVIDING <span>MEP EXPERTISE</span><br>FROM CONCEPT TO MAINTENANCE</h1>
  <div class="underline" style="left:580px;top:261px"></div>
  <p class="abs hero-text">Reliable plumbing services for residential clients and large-scale commercial projects.</p>
  <div class="btn btn-light" style="left:580px;top:398px;width:185px;height:42px">REQUEST SERVICE</div>
  <svg class="abs" style="left:0;top:470px" width="1200" height="130" viewBox="0 0 1200 130">
    <polygon points="0,0 600,60 1200,52 1200,130 0,130" fill="#1e1e1f"/>
    <polygon points="0,0 600,60 0,75" fill="var(--blue)"/>
    <polygon points="0,75 600,60 1200,130 0,130" fill="var(--white)"/>
  </svg>
</section>

<!-- ABOUT -->
<div class="abs about-head" style="left:112px;top:614px">
  <h2 class="h2">ABOUT VELOTRIN</h2><span class="rule"></span>
</div>
<div class="abs about-text">
  <p>Velotrin we provide dependable, professional plumbing services for commercial properties, construction projects, and residential clients. Our team combines technical expertise with a commitment to fast response times, quality workmanship, and long-term reliability.</p>
  <p>We understand that plumbing systems are critical to the operation of businesses and the comfort of homes. That’s why we approach every project—from routine maintenance to complex system installations.</p>
</div>
<div class="btn btn-dark" style="left:112px;top:1025px;width:186px;height:43px">MORE ABOUT US</div>
<svg class="abs" style="left:1018px;top:640px" width="92" height="176" aria-hidden="true">
  <defs><pattern id="dots" width="11" height="11" patternUnits="userSpaceOnUse"><circle cx="2" cy="2" r="1.6" fill="#071826"/></pattern></defs>
  <path d="M0 0H92V176H80V12H0Z" fill="url(#dots)"/>
</svg>
<div class="ph" role="img" aria-label="Plumber in blue shirt repairing pipes under a sink" style="left:610px;top:659px;width:479px;height:382px;border-radius:0 0 0 90px;background:linear-gradient(135deg,#e6ebef 0%,#c6d0d8 40%,#2d6fc4 70%,#1f4f94)"></div>

<!-- SERVICES -->
<svg class="abs" style="left:0;top:1140px" width="1200" height="650" viewBox="0 0 1200 650">
  <polygon points="0,4 1200,28 1200,646 0,646" fill="#071826"/>
  <polygon points="560,10 1200,0 1200,28" fill="#2a6cb0"/>
  <polygon points="0,615 700,642 0,646" fill="#2a6cb0"/>
  <polygon points="0,646 700,642 1200,646 1200,650 0,650" fill="#ffffff"/>
</svg>
<h2 class="abs h2" style="left:0;width:1200px;top:1225px;text-align:center;color:var(--white)">VT SERVICES</h2>
<div class="underline" style="left:572px;top:1266px"></div>
<svg class="abs" style="left:33px;top:1414px" width="40" height="28" aria-hidden="true"><circle cx="20" cy="14" r="12" fill="none" stroke="#fff" stroke-width="1.5"/><path d="M2 14H30M9 8 2 14 9 20" fill="none" stroke="#fff" stroke-width="1.5"/></svg>
<svg class="abs" style="left:1123px;top:1414px" width="40" height="28" aria-hidden="true"><circle cx="20" cy="14" r="12" fill="none" stroke="#fff" stroke-width="1.5"/><path d="M10 14H38M31 8 38 14 31 20" fill="none" stroke="#fff" stroke-width="1.5"/></svg>

<article class="card" style="left:114px">
  <div class="ph" role="img" aria-label="Worker assembling black commercial pipework" style="background:linear-gradient(135deg,#d8dce0,#3b3f45 50%,#2d55a0)"></div>
  <h3>COMMERCIAL PLUMBING</h3>
  <p>We provide comprehensive plumbing services for commercial</p>
  <svg class="circle-btn" viewBox="0 0 29 29"><path d="M12 9l5 5.5-5 5.5" fill="none" stroke="#071826" stroke-width="2.5"/></svg>
</article>
<article class="card" style="left:450px">
  <div class="ph" role="img" aria-label="Gloved hands tightening a leaking pipe" style="background:linear-gradient(135deg,#8a939c,#cfd3d6 50%,#2a4f8a)"></div>
  <h3>EMERGENCY PLUMBING</h3>
  <p>Plumbing emergencies can happen at any time and often require</p>
  <svg class="circle-btn" viewBox="0 0 29 29"><path d="M12 9l5 5.5-5 5.5" fill="none" stroke="#071826" stroke-width="2.5"/></svg>
</article>
<article class="card" style="left:785px">
  <div class="ph" role="img" aria-label="Workers in hard hats inspecting pipe fittings for leaks" style="background:linear-gradient(135deg,#e2711f,#c9a62d 45%,#4a5a4a)"></div>
  <h3>LEAK DETECTION &amp; REPAIR</h3>
  <p>Hidden leaks can lead to structural damage, mold growth, and high water</p>
  <svg class="circle-btn" viewBox="0 0 29 29"><path d="M12 9l5 5.5-5 5.5" fill="none" stroke="#071826" stroke-width="2.5"/></svg>
</article>

<!-- WHY CHOOSE -->
<h2 class="abs h2" style="left:0;width:1200px;top:1850px;text-align:center;color:var(--navy)">WHY CHOOSE US VELOTRIN</h2>
<div class="underline" style="left:572px;top:1902px"></div>

<svg class="abs" style="left:128px;top:1918px" width="58" height="58" fill="none" stroke="#1b1f24" stroke-width="1.6" aria-hidden="true"><path d="M6 8l2 4 4 .5-3 3 1 4-4-2-4 2 1-4-3-3 4-.5zM28 4l2 4 4 .5-3 3 1 4-4-2-4 2 1-4-3-3 4-.5zM48 8l2 4 4 .5-3 3 1 4-4-2-4 2 1-4-3-3 4-.5z"/><circle cx="24" cy="32" r="7"/><path d="M10 54c0-10 6-14 14-14 5 0 8 1 10 3"/><circle cx="44" cy="48" r="8"/><path d="M40 48l3 3 5-6"/></svg>
<div class="why-item" style="left:128px;top:2004px"><h4>LICENSED PROFESSIONALS</h4><p>Our certified plumbers have extensive experience in residential and commercial plumbing systems</p></div>

<svg class="abs" style="left:798px;top:1918px" width="58" height="58" fill="none" stroke="#1b1f24" stroke-width="1.6" aria-hidden="true"><circle cx="32" cy="20" r="10"/><path d="M16 56V46c0-8 7-12 16-12s16 4 16 12v10zM27 44h10v8H27z"/><rect x="2" y="4" width="14" height="10" rx="3"/></svg>
<div class="why-item" style="left:800px;top:2004px"><h4>SAME-DAY SERVICE</h4><p>We know hot water issues can’t wait. That’s why we offer same-day service whenever possible.</p></div>

<div class="abs" style="left:113px;top:2171px;width:340px;height:1px;background:var(--line)"></div>
<div class="abs" style="left:745px;top:2171px;width:343px;height:1px;background:var(--line)"></div>

<svg class="abs" style="left:128px;top:2206px" width="58" height="58" fill="none" stroke="#1b1f24" stroke-width="1.6" aria-hidden="true"><path d="M29 4l11 4v9c0 8-5 12-11 15-6-3-11-7-11-15V8z"/><path d="M24 17l4 4 6-7"/><path d="M4 30l6 18 10 6M54 30l-6 18-10 6M10 36l8 10M48 36l-8 10"/></svg>
<div class="why-item" style="left:128px;top:2291px"><h4>FAST EMERGENCY RESPONSE</h4><p>Plumbing emergencies can’t wait. Our rapid response team is available to resolve urgent issues quickly.</p></div>

<svg class="abs" style="left:798px;top:2206px" width="58" height="58" fill="none" stroke="#1b1f24" stroke-width="1.6" aria-hidden="true"><path d="M29 3l6 4 7-1 3 7 6 4-2 7 2 7-6 4-3 7-7-1-6 4-6-4-7 1-3-7-6-4 2-7-2-7 6-4 3-7 7 1z"/><circle cx="29" cy="30" r="15"/><path d="M22 30l5 5 9-10"/></svg>
<div class="why-item" style="left:800px;top:2291px"><h4>BEST PRICE GUARANTEE</h4><p>You’ll receive fair, transparent pricing with no surprises. If you find a better comparable price, we’ll match it.</p></div>

<svg class="abs" style="left:455px;top:1965px" width="290" height="400" viewBox="0 0 290 400" aria-hidden="true">
  <g stroke="#2a6cb0" stroke-width="2" fill="#2a6cb0">
    <line x1="28" y1="10" x2="76" y2="87"/><circle cx="28" cy="10" r="4"/><circle cx="76" cy="87" r="4"/>
    <line x1="265" y1="10" x2="217" y2="87"/><circle cx="265" cy="10" r="4"/><circle cx="217" cy="87" r="4"/>
    <line x1="6" y1="390" x2="62" y2="325"/><circle cx="6" cy="390" r="4"/><circle cx="62" cy="325" r="4"/>
    <line x1="286" y1="390" x2="230" y2="325"/><circle cx="286" cy="390" r="4"/><circle cx="230" cy="325" r="4"/>
  </g>
  <circle cx="145" cy="207" r="133" fill="none" stroke="#2a6cb0" stroke-width="1.2" stroke-dasharray="3 3"/>
  <circle cx="145" cy="207" r="120" fill="#dce9f5"/>
  <circle cx="145" cy="207" r="106" fill="#071826"/>
</svg>
<div class="abs brand" style="left:520px;top:2159px;color:var(--white);font-size:24px"><span class="brand-mark" style="width:20px;height:20px"></span>VELOTRIN</div>
<div class="btn btn-dark" style="left:486px;top:2434px;width:228px;height:42px">CALL OUR TEAM TODAY</div>

<!-- BLOG -->
<svg class="abs" style="left:0;top:2540px" width="1200" height="735" viewBox="0 0 1200 735">
  <polygon points="0,5 1200,30 1200,735 0,735" fill="#071826"/>
  <polygon points="0,0 500,20 0,26" fill="#2a6cb0"/>
  <polygon points="0,5 500,20 1200,30 1200,0" fill="#ffffff"/>
  <polygon points="520,712 1200,700 1200,735" fill="#2a6cb0"/>
  <polygon points="0,735 520,712 1200,735" fill="#ffffff"/>
</svg>
<h2 class="abs h2" style="left:0;width:1200px;top:2622px;text-align:center;color:var(--white)">LATEST NEWS &amp; BLOG</h2>
<div class="underline" style="left:572px;top:2680px"></div>
<svg class="abs" style="left:90px;top:2712px" width="95" height="170" aria-hidden="true">
  <defs><pattern id="dotsw" width="11" height="11" patternUnits="userSpaceOnUse"><circle cx="2" cy="2" r="1.4" fill="#8fa0b3"/></pattern></defs>
  <path d="M0 0H95V12H12V170H0Z" fill="url(#dotsw)"/>
</svg>
<svg class="abs" style="left:1015px;top:2820px" width="95" height="170" aria-hidden="true">
  <defs><pattern id="dotsw2" width="11" height="11" patternUnits="userSpaceOnUse"><circle cx="2" cy="2" r="1.4" fill="#8fa0b3"/></pattern></defs>
  <path d="M83 0H95V170H0V158H83Z" fill="url(#dotsw2)"/>
</svg>

<article class="post" style="left:113px">
  <div class="ph" role="img" aria-label="Worker in hard hat fitting valves on a wall of pipes" style="background:linear-gradient(135deg,#cfd2d4,#7a7f86 50%,#2a4f8a)"></div>
  <span class="date">NOV 17, 2025</span>
  <p>Velotrin Construction, Inc. (VT), a leader in mechanical, electrical, and plumbing construction and modular innovation</p>
</article>
<article class="post" style="left:448px">
  <div class="ph" role="img" aria-label="Gloved hands adjusting brass manifold fittings" style="background:linear-gradient(135deg,#e5e7e9,#b7924a 45%,#c83a3a)"></div>
  <span class="date">AUG 28, 2025</span>
  <p>If you’re not familiar with an Electrical Maintenance Program (EMP), it’s essentially a documented plan for proactively</p>
</article>
<article class="post" style="left:783px">
  <div class="ph" role="img" aria-label="Plumber tightening chrome pipes with a wrench" style="background:linear-gradient(135deg,#eef0f2,#a8adb2 45%,#2e3a4a)"></div>
  <span class="date">MAY 21, 2025</span>
  <p>With decades-long experience in the industry, VT can attest to the devastating consequences of mechanical, electrical</p>
</article>
<div class="btn btn-light" style="left:503px;top:3141px;width:193px;height:42px">VIEW MORE BLOGS</div>

<!-- FOOTER -->
<div class="abs brand" style="left:0;width:1200px;justify-content:center;top:3335px;color:var(--navy);font-size:28px"><span class="brand-mark" style="width:24px;height:24px"></span>VELOTRIN</div>
<div class="abs foot-links">VT SERVICE &nbsp;&nbsp;|&nbsp;&nbsp; VT MEP &nbsp;&nbsp;|&nbsp;&nbsp; PROJECTS &nbsp;&nbsp;|&nbsp;&nbsp; CAREERS &nbsp;&nbsp;|&nbsp;&nbsp; ABOUT</div>
<div class="abs" style="left:0;width:1200px;top:3457px;text-align:center;font-size:13.5px;color:var(--navy)">© 2026 VELOTRIN CONSTRUCTION, INC. | VT MEP, LLC | VT SERVICE, LLC</div>
<span class="social" style="left:502px"></span>
<span class="social" style="left:542px"></span>
<span class="social" style="left:582px"></span>
<span class="social" style="left:622px"></span>
<span class="social" style="left:662px"></span>

</body>
</html>
```